Home page design for Drone video business (the Business focusses on home videos for realtors)

Dear reader,

*I NEED DESIGNS OF ALL THE PAGES*
We need a first design of a homepage and of 4 other pages of the website of a business that sells drone video services. All the pages will need to be in the similar design style.
The video's are targeted at consumers that want to sell there home and would like to have a cool drone video of photos of their home.

How does the website look:
- has a navbar on top
- A cool looking banner of an areal drone.
- A Big header: with company name: SkyLoftReels
- A smaller subheader: We film your home to increase your chances of sale
- Then a section with a Big header: How does it work
- In this section a place for a vimeo explainitory video
- Then a similar navbar styled bar with a phone number and a email address
- Then a section where the videos porfolio is displayed in a cool way
- Inside this sectiona header: Our work

- A section with header: Why us?
- 4 symbols here with a subheader and some lorum ipsum text underneath (see wireframe images)

- Under that a: Contact us
- where you can put in name, email, phone, message box and a send button

- At the bottom a footer with phone number and a fake address for now.

Be creative. Use creative but serious color.
Use a serious font. Make it a sharp design. Sharp lines. Not to dark design and not to light design.

The wireframes are the same kind of images.
PLEASE PUT IN DESIGNS OF ALL THE PAGES

Good luck

Target Market(s)

People that want to sell home and want to make a cool drone video or photos of their home.

Industry/Entity Type

Business

Contact Information for Business Card

Lucas Wenning
lucas@skyloftreels.example
+31647208351

Logo Text

SkyLoftReels

Number of Pages Required

1 page

Font styles to use
Sans Serif

Requirements
Must have
• All the sections as explained in the instructions.
• The nav bar should have an about us, services, portfolio and a contact us buttons.
• See instruction for details.
• Must include designs of the front page, contact us, our services, portfolio and contact us.
• If you do add some designs for the "about us", "services", "prices", "portfolio" and "contact us" pages, you make a way better chance of winning the competition.
Nice to have
• designs for the other pages as described at the Must haves. You make a better chance of winning if you include them. Look at the wireframes to see the mockups for those pages. think creative about what kind of sections and design should be included in those pages.
Should not have
• bad designs.

```html
<!DOCTYPE html>
<html lang="en">
<head>
<meta charset="utf-8">
<title>SkyLoftReels – Home</title>
<link href="https://fonts.googleapis.com/css2?family=Oswald:wght@400;500&family=Roboto:wght@400;500&display=swap" rel="stylesheet">
<style>
:root{
  --blue:#2a93c9;
  --blue-deep:#1a86c4;
  --bar-left:#39a6d9;
  --bar-right:#4fb9e7;
  --ink:#222;
  --paper:#f0f0f0;
  --white:#fff;
  --line:#cfcfcf;
  --footer:#1c1c1c;
}
*{box-sizing:border-box;margin:0;padding:0}
html,body{width:1200px;height:2795px;overflow:hidden}
body{position:relative;background:var(--paper);font-family:'Roboto',sans-serif;color:var(--ink)}
.abs{position:absolute}
.heading{font-family:'Oswald',sans-serif;font-weight:400;font-size:36px;color:var(--blue);text-align:center;width:100%;letter-spacing:.3px}

/* nav */
.topnav{left:0;top:0;width:1200px;height:99px;background:var(--white);box-shadow:0 2px 4px rgba(0,0,0,.15);z-index:2}
.brand{left:86px;top:30px;display:flex;align-items:center;gap:12px;font-family:'Oswald',sans-serif;font-size:27px;color:var(--ink)}
.brand-dot{width:40px;height:40px;border:3px solid var(--blue);border-radius:50%}
.menu{right:92px;top:41px;display:flex;gap:54px;font-size:15px;list-style:none}
.menu li.active{color:var(--blue)}

/* hero */
.hero{left:0;top:99px;width:1200px;height:557px;background:radial-gradient(ellipse at 75% 40%,#5a6a5a 0%,#2c3a30 45%,#16211c 100%)}
.hero-title{left:88px;top:232px;font-family:'Oswald',sans-serif;font-size:52px;color:var(--white);font-weight:400}
.hero-sub{left:88px;top:300px;font-size:34px;line-height:42px;color:var(--white)}
.dots{left:558px;top:500px;display:flex;gap:6px}
.dots span{width:11px;height:11px;border-radius:50%;background:var(--white)}
.dots span.on{background:var(--blue)}

/* how */
.video{left:194px;top:758px;width:812px;height:421px;border:4px solid var(--white);box-shadow:0 0 6px rgba(0,0,0,.2);background:linear-gradient(180deg,#b7c2c8 0%,#6c8a5c 30%,#4f7040 70%,#7a8a80 100%)}
.vtools{right:10px;top:30px;display:flex;flex-direction:column;gap:6px}
.vtool{width:52px;height:44px;background:rgba(20,20,20,.75);color:var(--white);font-size:10px;font-weight:500;display:flex;flex-direction:column;align-items:center;justify-content:center;gap:3px}
.vcontrols{left:58px;bottom:14px;right:40px;height:46px;display:flex;align-items:center;gap:14px}
.vplay{width:90px;height:50px;background:rgba(20,20,20,.85);display:flex;align-items:center;justify-content:center}
.vtrack{flex:1;height:14px;background:rgba(20,20,20,.8);position:relative}
.vtrack i{position:absolute;left:0;top:0;height:14px;width:46%;background:var(--blue)}
.vtime{position:absolute;left:44%;top:-22px;background:var(--white);color:#111;font-size:11px;padding:1px 4px}
.vhd{color:var(--blue);font-weight:500;font-size:14px;font-style:italic}

/* contact bar */
.cbar{left:0;top:1230px;width:1200px;height:85px;display:flex}
.cbar div{flex:1;display:flex;align-items:center;justify-content:center;gap:16px;color:var(--white);font-size:34px}
.cbar .phone{background:var(--bar-left)}
.cbar .mail{background:var(--bar-right)}

/* work */
.work{left:0;top:1315px;width:1200px;height:436px;background:var(--white)}
.thumbs{left:88px;top:123px;display:flex;gap:14px}
.thumb{width:246px;height:250px;border:4px solid var(--white);box-shadow:0 0 6px rgba(0,0,0,.25);position:relative}
.thumb .play{position:absolute;left:50%;top:50%;transform:translate(-50%,-50%);width:62px;height:38px;background:rgba(20,20,20,.8);display:flex;align-items:center;justify-content:center}
.t1{background:linear-gradient(160deg,#b9d7ea,#8c8c6a 55%,#6a7f4c)}
.t2{background:linear-gradient(180deg,#a9c3d9,#7a8e62 40%,#8a6b58)}
.t3{background:linear-gradient(180deg,#6fb0e2,#86b6c8 50%,#4c7b3a)}
.t4{background:linear-gradient(180deg,#5b7b4a,#8a9e6a 55%,#6d6354)}

/* why */
.why{left:0;top:1751px;width:1200px;height:460px;background:radial-gradient(ellipse at 60% 40%,#2e9bd6 0%,var(--blue-deep) 70%)}
.why .heading{color:var(--white);top:46px;position:absolute}
.feature{width:420px;height:120px}
.ficon{left:0;top:0;width:75px;height:67px;background:var(--white);border-radius:4px;box-shadow:0 2px 4px rgba(0,0,0,.2);display:flex;align-items:center;justify-content:center}
.ftitle{left:84px;top:6px;font-family:'Oswald',sans-serif;font-size:21px;color:var(--white)}
.ftext{left:84px;top:40px;width:345px;font-size:12px;line-height:19px;color:var(--white);text-align:justify}
.fmore{left:84px;top:104px;font-size:11px;color:var(--white)}

/* contact form */
.contact .heading{position:absolute;top:2262px}
.field{background:var(--white);border:2px solid #d6d6d6;box-shadow:inset 0 0 0 2px #f7f7f7;font-size:12px;color:#555;padding:14px 14px}
.send{left:453px;top:2552px;width:294px;height:66px;background:linear-gradient(180deg,#4fb5e6,#2b8fc9);color:var(--white);font-size:22px;display:flex;align-items:center;justify-content:center;border-radius:3px}

/* footer */
.footline{left:0;top:2683px;width:1200px;height:11px;background:var(--blue)}
.footer{left:0;top:2694px;width:1200px;height:101px;background:var(--footer);color:var(--white)}
.fphone{left:88px;top:32px;font-size:17px;font-weight:500;display:flex;align-items:center;gap:10px}
.faddr{left:88px;top:60px;font-size:11px}
.fcopy{left:0;width:1200px;top:44px;text-align:center;font-size:11px}
.fbrand{right:110px;top:32px;display:flex;align-items:center;gap:10px;font-family:'Oswald',sans-serif;font-size:22px}
.fbrand .brand-dot{width:32px;height:32px;border-color:var(--white);border-width:2px}
</style>
</head>
<body>

<header class="abs topnav">
  <div class="abs brand"><span class="brand-dot"></span>SkyLoftReels</div>
  <ul class="abs menu">
    <li class="active">HOME</li><li>SERVICES</li><li>ABOUT US</li><li>PORTFOLIO</li><li>CONTACTS</li>
  </ul>
</header>

<section class="abs hero" role="img" aria-label="Banner photo of a white camera drone flying in front of blurred trees"></section>
<h1 class="abs hero-title">SKYLOFTREELS</h1>
<p class="abs hero-sub">We film your home to increase<br>your chances of sale</p>
<div class="abs dots"><span class="on"></span><span></span><span></span><span></span><span></span></div>

<h2 class="abs heading" style="top:688px">HOW DOES IT WORK?</h2>
<div class="abs video" role="img" aria-label="Explainer video player showing an aerial view of a city park">
  <div class="abs vtools">
    <div class="vtool"><svg width="16" height="14" viewBox="0 0 16 14"><path d="M8 14 1.5 7.5A3.8 3.8 0 0 1 8 2.5a3.8 3.8 0 0 1 6.5 5Z" fill="#fff"/></svg>LIKE</div>
    <div class="vtool"><svg width="16" height="14" viewBox="0 0 16 14" fill="#fff"><circle cx="3" cy="7" r="2.2"/><circle cx="13" cy="2.5" r="2.2"/><circle cx="13" cy="11.5" r="2.2"/><path d="M3 7 13 2.5M3 7l10 4.5" stroke="#fff" stroke-width="1.3"/></svg>SHARE</div>
    <div class="vtool"><svg width="18" height="12" viewBox="0 0 18 12" fill="none" stroke="#fff" stroke-width="2"><path d="M5 2 1 6l4 4M13 2l4 4-4 4M10 1 8 11"/></svg>EMBED</div>
  </div>
  <div class="abs vcontrols">
    <div class="vplay"><svg width="18" height="20" viewBox="0 0 18 20"><path d="M2 1 17 10 2 19Z" fill="#fff"/></svg></div>
    <div class="vtrack"><i></i><span class="vtime">00:34</span></div>
    <span class="vhd">HD</span>
    <svg width="14" height="14" viewBox="0 0 14 14" fill="none" stroke="#fff" stroke-width="2"><path d="M1 5V1h4M9 1h4v4M13 9v4H9M5 13H1V9"/></svg>
  </div>
</div>

<div class="abs cbar">
  <div class="phone"><svg width="30" height="30" viewBox="0 0 30 30"><rect width="30" height="30" rx="4" fill="#fff"/><path d="M9 7c1-1 2-1 3 0l2 3c.5 1 0 2-1 2.5 1 2 2.5 3.5 4.5 4.5.5-1 1.5-1.5 2.5-1l3 2c1 1 1 2 0 3-2 2-5 2-9-2S7 9 9 7Z" fill="var(--bar-left)"/></svg>+31647208351</div>
  <div class="mail"><svg width="34" height="24" viewBox="0 0 34 24"><rect width="34" height="24" rx="2" fill="#fff"/><path d="M1 2 17 14 33 2" fill="none" stroke="var(--bar-right)" stroke-width="2.5"/></svg>contact@skyloftreels.example</div>
</div>

<section class="abs work">
  <h2 class="abs heading" style="top:48px">OUR WORK</h2>
  <div class="abs thumbs">
    <div class="thumb t1" role="img" aria-label="Aerial video of a small town seen from a drone"><span class="play"><svg width="12" height="14" viewBox="0 0 12 14"><path d="M1 1 11 7 1 13Z" fill="#fff"/></svg></span></div>
    <div class="thumb t2" role="img" aria-label="Aerial video of a residential neighbourhood"><span class="play"><svg width="12" height="14" viewBox="0 0 12 14"><path d="M1 1 11 7 1 13Z" fill="#fff"/></svg></span></div>
    <div class="thumb t3" role="img" aria-label="Video of a drone flying over a lake and forest"><span class="play"><svg width="12" height="14" viewBox="0 0 12 14"><path d="M1 1 11 7 1 13Z" fill="#fff"/></svg></span></div>
    <div class="thumb t4" role="img" aria-label="Aerial video of a detached house with garden"><span class="play"><svg width="12" height="14" viewBox="0 0 12 14"><path d="M1 1 11 7 1 13Z" fill="#fff"/></svg></span></div>
  </div>
</section>

<section class="abs why" role="region" aria-label="Why us">
  <h2 class="heading">WHY US?</h2>

  <div class="abs feature" style="left:108px;top:138px">
    <div class="abs ficon"><svg width="30" height="26" viewBox="0 0 30 26" fill="none" stroke="var(--blue)" stroke-width="2"><rect x="9" y="2" width="12" height="10"/><rect x="2" y="14" width="12" height="10"/><rect x="16" y="14" width="12" height="10"/></svg></div>
    <h3 class="abs ftitle">CHEAP</h3>
    <p class="abs ftext">Lorem Ipsum has been the industry's standard dummy text ever since the 1500s, when an unknown printer took a galley of type and scrambled it to make</p>
    <span class="abs fmore">Read More &raquo;</span>
  </div>
  <div class="abs feature" style="left:650px;top:138px">
    <div class="abs ficon"><svg width="28" height="28" viewBox="0 0 28 28" fill="none" stroke="var(--blue)" stroke-width="2.5"><circle cx="14" cy="14" r="11"/><circle cx="14" cy="14" r="5"/><path d="M6 6l4.5 4.5M22 6l-4.5 4.5M6 22l4.5-4.5M22 22l-4.5-4.5"/></svg></div>
    <h3 class="abs ftitle">FLEXIBLE</h3>
    <p class="abs ftext">Lorem Ipsum has been the industry's standard dummy text ever since the 1500s, when an unknown printer took a galley of type and scrambled it to make</p>
    <span class="abs fmore">Read More &raquo;</span>
  </div>
  <div class="abs feature" style="left:108px;top:280px">
    <div class="abs ficon"><svg width="30" height="26" viewBox="0 0 30 26"><rect x="2" y="2" width="26" height="16" fill="none" stroke="var(--blue)" stroke-width="2.5"/><path d="M11 24h8M15 18v6" stroke="var(--blue)" stroke-width="2.5"/></svg></div>
    <h3 class="abs ftitle">9K QUALITY</h3>
    <p class="abs ftext">Lorem Ipsum has been the industry's standard dummy text ever since the 1500s, when an unknown printer took a galley of type and scrambled it to make</p>
    <span class="abs fmore">Read More &raquo;</span>
  </div>
  <div class="abs feature" style="left:650px;top:280px">
    <div class="abs ficon"><svg width="28" height="26" viewBox="0 0 28 26"><path d="M27 1 1 12l9 3 2 10 4-6 7 5Z" fill="var(--blue)"/></svg></div>
    <h3 class="abs ftitle">INCREASE SALE CHANCE</h3>
    <p class="abs ftext">Lorem Ipsum has been the industry's standard dummy text ever since the 1500s, when an unknown printer took a galley of type and scrambled it to make</p>
    <span class="abs fmore">Read More &raquo;</span>
  </div>
</section>

<section class="contact">
  <h2 class="heading">CONTACT US</h2>
  <div class="abs field" style="left:199px;top:2340px;width:252px;height:54px">Name</div>
  <div class="abs field" style="left:473px;top:2340px;width:252px;height:54px">Email id</div>
  <div class="abs field" style="left:747px;top:2340px;width:252px;height:54px">Phone</div>
  <div class="abs field" style="left:199px;top:2405px;width:802px;height:125px">Message</div>
  <div class="abs send">SEND</div>
</section>

<div class="abs footline"></div>
<footer class="abs footer">
  <div class="abs fphone"><svg width="16" height="16" viewBox="0 0 30 30"><rect width="30" height="30" rx="4" fill="#fff"/><path d="M9 7c1-1 2-1 3 0l2 3c.5 1 0 2-1 2.5 1 2 2.5 3.5 4.5 4.5.5-1 1.5-1.5 2.5-1l3 2c1 1 1 2 0 3-2 2-5 2-9-2S7 9 9 7Z" fill="var(--footer)"/></svg>+31647208351</div>
  <div class="abs faddr">Address : 120 Harbor Lane, Fairview Bay, NJ</div>
  <div class="abs fcopy">Copyright &copy; 2016 &nbsp;All Rights</div>
  <div class="abs fbrand"><span class="brand-dot"></span>SkyLoftReels</div>
</footer>

</body>
</html>
```